Corvel Capital LLC

Need Professional Business cards for New Investment Fund

Target Market(s)

High Quality investors

Industry/Entity Type

Financial

Contact Information for Business Card

Phone Number +1 555 284 6190
Name Lukas Varenko
Title Fund Manager
email lv@FundCorvel.com
Website www.FundCorvel.com

Colors

Designer to choose colors to be used in the design.

Requirements
Must have
• Must have our Logo and all of the above. Must be made so lettering and loge can be raised

```html
<!DOCTYPE html>
<html lang="en">
<head>
<meta charset="utf-8">
<title>Fund Manager Business Card</title>
<link href="https://fonts.googleapis.com/css2?family=Oswald:wght@300;400;600&display=swap" rel="stylesheet">
<style>
  :root {
    --backdrop: #69696b;
    --ink-black: #000000;
    --paper-light: #ffffff;
    --paper-shade: #e4e4e6;
    --brand-green: #7ee23a;
    --brand-slate: #424a3e;
    --text-white: #ffffff;
  }
  html, body {
    margin: 0;
    padding: 0;
    width: 1200px;
    height: 1200px;
    overflow: hidden;
    background: var(--backdrop);
    font-family: "Oswald", "Arial Narrow", sans-serif;
  }
  .stage {
    position: relative;
    width: 1200px;
    height: 1200px;
  }
  .card {
    position: absolute;
    left: 250px;
    width: 700px;
    height: 400px;
    overflow: hidden;
  }
  .card--front { top: 147px; }
  .card--back { top: 652px; background: var(--ink-black); }
  .card__shapes {
    position: absolute;
    inset: 0;
    width: 700px;
    height: 400px;
  }
  .brand {
    position: absolute;
    display: flex;
    align-items: center;
    gap: 9px;
  }
  .brand__mark {
    background: var(--brand-green);
  }
  .brand__name {
    color: var(--brand-slate);
    font-weight: 400;
    letter-spacing: 0.04em;
    text-transform: uppercase;
    line-height: 1;
  }
  .card--front .brand {
    left: 296px;
    top: 244px;
  }
  .card--front .brand__mark { width: 20px; height: 20px; }
  .card--front .brand__name { font-size: 32px; }
  .card--back .brand {
    left: 36px;
    top: 140px;
  }
  .card--back .brand__mark { width: 13px; height: 13px; }
  .card--back .brand__name { font-size: 19px; }
  .website {
    position: absolute;
    right: 47px;
    top: 352px;
    margin: 0;
    color: var(--brand-green);
    font-weight: 400;
    font-size: 19px;
    line-height: 1.2;
    letter-spacing: 0.07em;
  }
  .contact {
    position: absolute;
    left: 36px;
    top: 233px;
    color: var(--text-white);
  }
  .contact__name {
    margin: 0;
    font-weight: 600;
    font-size: 24px;
    letter-spacing: 0.05em;
    line-height: 1.2;
  }
  .contact__title {
    margin: 2px 0 0;
    font-weight: 400;
    font-size: 17px;
    letter-spacing: 0.04em;
  }
  .contact__lines {
    margin: 14px 0 0;
    font-weight: 400;
    font-size: 17px;
    letter-spacing: 0.08em;
    line-height: 27px;
  }
</style>
</head>
<body>
<main class="stage">

  <section class="card card--front" aria-label="Card front">
    <svg class="card__shapes" viewBox="0 0 700 400" aria-hidden="true">
      <defs>
        <linearGradient id="paperFront" x1="0" y1="0" x2="1" y2="1">
          <stop offset="0" stop-color="#ffffff"/>
          <stop offset="1" stop-color="#e4e4e6"/>
        </linearGradient>
      </defs>
      <rect width="700" height="400" fill="url(#paperFront)"/>
      <polygon points="0,0 109,0 109,291 185,291 102,400 0,400" fill="#000000"/>
    </svg>
    <div class="brand">
      <span class="brand__mark"></span>
      <span class="brand__name">Calvenor</span>
    </div>
    <p class="website">www.FundCorvel.com</p>
  </section>

  <section class="card card--back" aria-label="Card back">
    <svg class="card__shapes" viewBox="0 0 700 400" aria-hidden="true">
      <defs>
        <linearGradient id="paperBack" x1="0" y1="0" x2="0" y2="1">
          <stop offset="0" stop-color="#f2f2f3"/>
          <stop offset="1" stop-color="#e4e4e6"/>
        </linearGradient>
      </defs>
      <polygon points="615,0 700,0 700,400 596,400 596,150 517,150" fill="url(#paperBack)"/>
    </svg>
    <div class="brand">
      <span class="brand__mark"></span>
      <span class="brand__name">Calvenor</span>
    </div>
    <div class="contact">
      <p class="contact__name">Lukas Varenko</p>
      <p class="contact__title">Fund Manager</p>
      <p class="contact__lines">T: +1 555 284 6190<br>E: lv@FundCorvel.com</p>
    </div>
  </section>

</main>
</body>
</html>
```